FinTech company looking to revamp and expand client-facing interface for our financial models

Pellworth Engines currently has a very simple website that allows clients to interact with our financial models. We are looking to completely redesign the current site and add several extra pages to provide extra functionality. We want the design to have a modern, slick feel, that will work on both a desktop or a tablet. It should be straightforward for clients to move between different pages at any time, and clear from the layout how to interact with the more advanced features. We have included screenshots of existing pages in the attached design brief, as well as sketches of the functionality required by the new pages, but can't provide a direct link to the current site.
Target Market(s)
Professional investors that will be paying to access the interface
Industry/Entity Type
Finance
Number of Pages Required
4 page
Colors
Designer to choose colors to be used in the design.
Look and feel
Each slider illustrates characteristics of the customer's brand and the style your logo design should communicate.

```html
<!DOCTYPE html>
<html lang="en">
<head>
<meta charset="utf-8">
<title>Pellworth Engines – Portfolio</title>
<link href="https://fonts.googleapis.com/css2?family=Montserrat:wght@500;600;700&family=Roboto+Condensed:wght@400;500&display=swap" rel="stylesheet">
<style>
:root{
  --navy:#062e61;
  --teal:#05686a;
  --black:#1c1c1c;
  --green:#1ca21c;
  --bar-green:#00cc00;
  --bar-red:#f00000;
  --minus:#b3182a;
  --frame:#e6e6e6;
  --page:#efefef;
  --row-alt:#f1f1f1;
  --line:#e2e2e2;
  --text:#111;
  --blue-dot:#3e6eab;
  --olive-dot:#bcb634;
}
*{box-sizing:border-box;margin:0;padding:0}
html,body{width:1169px;height:1200px;overflow:hidden}
body{background:var(--frame);font-family:'Roboto Condensed',sans-serif;color:var(--text);position:relative}
.page{position:absolute;left:13px;top:13px;width:1143px;height:1174px;background:var(--page)}
.abs{position:absolute}

/* nav */
.nav{position:absolute;left:13px;top:13px;width:1143px;height:54px;background:#fff;font-family:'Montserrat',sans-serif;font-weight:700;font-size:13px;box-shadow:0 2px 6px rgba(0,0,0,.06)}
.nav .cell{position:absolute;top:0;height:54px;display:flex;align-items:center;justify-content:center;gap:8px;border-right:1px solid #ececec;letter-spacing:.1px}
.brand{font-size:17px}
.nav .active{background:var(--navy);color:#fff}
.nav svg{width:22px;height:22px}

/* panels */
.panel{position:absolute;background:#fff;box-shadow:0 2px 8px rgba(0,0,0,.12);overflow:hidden}
.panel-title{height:45px;display:flex;align-items:center;justify-content:center;color:#fff;font-family:'Montserrat',sans-serif;font-weight:600;font-size:15.5px}
.members .panel-title{background:var(--black);border-radius:4px 4px 0 0}
.col-head{display:flex;height:45px;background:var(--teal);color:#fff;font-family:'Montserrat',sans-serif;font-weight:600;font-size:15px}
.col-head div{display:flex;align-items:center;justify-content:center}
.col-name{width:234px;border-right:1px solid rgba(255,255,255,.35)}
.col-size{width:269px}
.row{display:flex;height:62px;font-size:17px}
.row:nth-child(even){background:var(--row-alt)}
.row .name{width:234px;display:flex;align-items:center;gap:18px;padding-left:45px;border-right:1px solid var(--line)}
.row .size{width:233px;display:flex;align-items:center;justify-content:center}
.scroll{position:absolute;right:0;top:90px;width:36px;height:378px;background:#d2d2d2}
.scroll .track{position:absolute;left:9px;top:20px;width:19px;height:350px;background:#fff;border-radius:10px}
.scroll .thumb{position:absolute;left:9px;top:22px;width:19px;height:68px;background:#909090;border-radius:10px}

.btn{position:absolute;top:589px;height:36px;display:flex;align-items:center;justify-content:center;gap:8px;color:#fff;font-family:'Montserrat',sans-serif;font-weight:700;font-size:13px;border-radius:3px}

.sens .panel-title{height:63px;background:var(--teal);font-size:16px}
.srow{height:63px;display:flex;align-items:center;font-size:17px}
.srow:nth-child(odd){background:#f3f3f3}
.srow .label{width:194px;padding-left:25px}
.barbox{position:relative;width:287px;height:50px;background:#e2e2e2}
.barbox .inner{position:absolute;left:9px;top:9px;width:269px;height:32px;background:#fff;border:1px solid #d5d5d5}
.barbox .grid{position:absolute;top:0;bottom:0;width:1px;background:#ececec}
.barbox .axis{position:absolute;left:143px;top:0;width:2px;height:50px;background:#777}
.barbox .fill{position:absolute;top:9px;height:32px}
.barbox .val{position:absolute;top:16px;font-size:17px}

.coll-btn{position:absolute;left:438px;top:679px;width:292px;height:36px;background:var(--navy);color:#fff;font-family:'Montserrat',sans-serif;font-weight:600;font-size:16px;display:flex;align-items:center;justify-content:center;border-radius:3px}

.chart-panel{left:63px;top:733px;width:1043px;height:382px;background:#fff}
.chart-top{position:absolute;left:0;top:0;width:1043px;height:76px;background:#ececec}
.tab{position:absolute;top:45px;height:31px;display:flex;align-items:center;justify-content:center;background:#fff;font-family:'Montserrat',sans-serif;font-weight:700;font-size:12.5px;color:#333}
.tab.chart{background:var(--navy);color:#fff}
.tab.current{background:var(--black);color:#fff;top:36px;height:40px;border-radius:3px 3px 0 0;align-items:flex-start;padding-top:14px}
.plot{position:absolute;left:0;top:76px}
</style>
</head>
<body>
<div class="page"></div>

<nav class="nav">
  <div class="cell brand" style="left:0;width:162px">PELLWORTH</div>
  <div class="cell" style="left:162px;width:81px">250D</div>
  <div class="cell" style="left:243px;width:81px">83D</div>
  <div class="cell" style="left:324px;width:81px">42D</div>
  <div class="cell" style="left:405px;width:122px"></div>
  <div class="cell" style="left:527px;width:126px;border-left:1px solid #ececec">
    <svg viewBox="0 0 24 24"><path d="M3 12 12 4l9 8M6 10v10h4v-6h4v6h4V10" fill="none" stroke="#111" stroke-width="2.4"/></svg>MODELS</div>
  <div class="cell" style="left:653px;width:159px">
    <svg viewBox="0 0 24 24"><g fill="#222"><circle cx="12" cy="12" r="3"/><circle cx="12" cy="3" r="1.6"/><circle cx="12" cy="21" r="1.6"/><circle cx="3" cy="12" r="1.6"/><circle cx="21" cy="12" r="1.6"/><circle cx="5.6" cy="5.6" r="1.6"/><circle cx="18.4" cy="18.4" r="1.6"/><circle cx="18.4" cy="5.6" r="1.6"/><circle cx="5.6" cy="18.4" r="1.6"/><circle cx="12" cy="7.5" r="1"/><circle cx="12" cy="16.5" r="1"/><circle cx="7.5" cy="12" r="1"/><circle cx="16.5" cy="12" r="1"/></g></svg>SENSITIVITIES</div>
  <div class="cell active" style="left:812px;width:145px">
    <svg viewBox="0 0 24 24"><g fill="none" stroke="#fff" stroke-width="1.8"><circle cx="6.5" cy="6.5" r="4"/><circle cx="17.5" cy="6.5" r="4"/><circle cx="6.5" cy="17.5" r="4"/><circle cx="17.5" cy="17.5" r="4"/></g></svg>PORTFOLIO</div>
  <div class="cell" style="left:957px;width:136px">
    <svg viewBox="0 0 24 24"><rect x="2" y="4" width="20" height="16" fill="none" stroke="#111" stroke-width="2"/><path d="M5 16l4-5 3 3 3-5 4 4" fill="none" stroke="#111" stroke-width="2"/></svg>BACKTEST</div>
</nav>

<!-- members -->
<section class="panel members" style="left:63px;top:103px;width:503px;height:468px;border-radius:4px">
  <div class="panel-title">Current Members</div>
  <div class="col-head"><div class="col-name">Members Name</div><div class="col-size">Size</div></div>
  <div class="rows">
    <div class="row"><div class="name"><svg width="22" height="22" viewBox="0 0 22 22"><circle cx="11" cy="11" r="9.5" fill="none" stroke="var(--minus)" stroke-width="2"/><path d="M6 11h10" stroke="var(--minus)" stroke-width="2"/></svg>Member 1</div><div class="size">0.2</div></div>
    <div class="row"><div class="name"><svg width="22" height="22" viewBox="0 0 22 22"><circle cx="11" cy="11" r="9.5" fill="none" stroke="var(--minus)" stroke-width="2"/><path d="M6 11h10" stroke="var(--minus)" stroke-width="2"/></svg>Member 2</div><div class="size">0.5</div></div>
    <div class="row"><div class="name"><svg width="22" height="22" viewBox="0 0 22 22"><circle cx="11" cy="11" r="9.5" fill="none" stroke="var(--minus)" stroke-width="2"/><path d="M6 11h10" stroke="var(--minus)" stroke-width="2"/></svg>Member 3</div><div class="size">-0.3</div></div>
    <div class="row"><div class="name"><svg width="22" height="22" viewBox="0 0 22 22"><circle cx="11" cy="11" r="9.5" fill="none" stroke="var(--minus)" stroke-width="2"/><path d="M6 11h10" stroke="var(--minus)" stroke-width="2"/></svg>Member 4</div><div class="size">0.2</div></div>
    <div class="row"><div class="name"><svg width="22" height="22" viewBox="0 0 22 22"><circle cx="11" cy="11" r="9.5" fill="none" stroke="var(--minus)" stroke-width="2"/><path d="M6 11h10" stroke="var(--minus)" stroke-width="2"/></svg>Member 5</div><div class="size">0.5</div></div>
    <div class="row"><div class="name"><svg width="22" height="22" viewBox="0 0 22 22"><circle cx="11" cy="11" r="9.5" fill="none" stroke="var(--minus)" stroke-width="2"/><path d="M6 11h10" stroke="var(--minus)" stroke-width="2"/></svg>Member 6</div><div class="size">-0.3</div></div>
  </div>
  <div class="scroll"><div class="track"></div><div class="thumb"></div></div>
</section>

<div class="btn" style="left:63px;width:152px;background:var(--navy)">
  <svg width="20" height="20" viewBox="0 0 20 20"><circle cx="10" cy="10" r="8.5" fill="none" stroke="#fff" stroke-width="1.6"/><path d="M10 5.5v9M5.5 10h9" stroke="#fff" stroke-width="1.6"/></svg>ADD A MEMBER</div>
<div class="btn" style="left:224px;width:157px;background:var(--green)">
  <svg width="22" height="20" viewBox="0 0 22 20"><path d="M2 11l6 6L20 3" fill="none" stroke="#fff" stroke-width="3.4"/></svg>SAVE PORTFOLIO</div>
<div class="btn" style="left:390px;width:119px;background:#333">
  <svg width="20" height="20" viewBox="0 0 20 20"><path d="M3 3l14 14M17 3 3 17" stroke="#fff" stroke-width="3"/></svg>CLEAR ALL</div>

<!-- sensitivities -->
<section class="panel sens" style="left:602px;top:103px;width:504px;height:315px;border-radius:4px 4px 0 0">
  <div class="panel-title">Sensitivities</div>
  <div class="srow"><div class="label">A-Lorem ipsum dolor</div>
    <div class="barbox"><div class="inner"></div><div class="grid" style="left:77px"></div><div class="grid" style="left:212px"></div>
      <div class="fill" style="left:144px;width:61px;background:var(--bar-green)"></div><div class="axis"></div><div class="val" style="left:216px">0.9</div></div></div>
  <div class="srow"><div class="label">B-Lorem ipsum dolor</div>
    <div class="barbox"><div class="inner"></div><div class="grid" style="left:77px"></div><div class="grid" style="left:212px"></div>
      <div class="fill" style="left:144px;width:49px;background:var(--bar-green)"></div><div class="axis"></div><div class="val" style="left:204px">0.7</div></div></div>
  <div class="srow"><div class="label">C-Lorem ipsum dolor</div>
    <div class="barbox"><div class="inner"></div><div class="grid" style="left:77px"></div><div class="grid" style="left:212px"></div>
      <div class="fill" style="left:107px;width:36px;background:var(--bar-red)"></div><div class="axis"></div><div class="val" style="left:76px">-0.6</div></div></div>
  <div class="srow"><div class="label">D-Lorem ipsum dolor</div>
    <div class="barbox"><div class="inner"></div><div class="grid" style="left:77px"></div><div class="grid" style="left:212px"></div>
      <div class="fill" style="left:126px;width:17px;background:var(--bar-red)"></div><div class="axis"></div><div class="val" style="left:95px">-0.3</div></div></div>
</section>

<div class="coll-btn">Properties of Collection</div>

<section class="panel chart-panel">
  <div class="chart-top"></div>
  <div class="tab chart" style="left:49px;width:140px">CHART</div>
  <div class="tab" style="left:193px;width:81px">#1</div>
  <div class="tab" style="left:279px;width:81px">#2</div>
  <div class="tab" style="left:364px;width:81px">#3</div>
  <div class="tab current" style="left:449px;width:81px">#4</div>

  <svg class="plot" width="1043" height="306" viewBox="0 0 1043 306" font-family="Montserrat, sans-serif" font-size="11" fill="#555">
    <g stroke="#eee">
      <path d="M101 50V225M229 50V225M355 50V225M481 50V225M605 50V225M732 50V225M857 50V225"/>
      <path d="M85 57H903M85 91H903M85 124H903M85 158H903M85 191H903"/>
    </g>
    <path d="M85 225H903" stroke="#555"/>
    <g text-anchor="end"><text x="73" y="61">100</text><text x="73" y="95">80</text><text x="73" y="128">60</text><text x="73" y="162">40</text><text x="73" y="195">20</text><text x="73" y="229">0</text></g>
    <g text-anchor="middle"><text x="101" y="251">Jul 2018</text><text x="229" y="251">Sep 2018</text><text x="355" y="251">Nov 2018</text><text x="481" y="251">Jan 2019</text><text x="605" y="251">Mar 2019</text><text x="732" y="251">May 2019</text><text x="857" y="251">Jul 2019</text></g>

    <path stroke="var(--olive-dot)" stroke-width="6" stroke-linecap="round" fill="none" d="M105 57h0M110 57h0M115 57h0M120 57h0M125 57h0M130 57h0M135 57h0M140 57h0M145 57h0M150 57h0M155 57h0M160 57h0M165 57h0M170 57h0M175 63h0M180 62h0M185 66h0M190 58h0M195 62h0M200 60h0M205 63h0M210 66h0M215 60h0M220 64h0M222 128h0M226 145h0M230 150h0M235 160h0M240 168h0M245 148h0M250 162h0M255 140h0M260 120h0M265 117h0M268 112h0M270 95h0M275 89h0M280 88h0M285 120h0M288 110h0M290 60h0M295 65h0M300 115h0M305 120h0M310 140h0M315 135h0M320 210h0M325 200h0M330 190h0M335 185h0M340 205h0M345 215h0M350 220h0M355 213h0M360 205h0M365 190h0M370 212h0M375 218h0M380 200h0M385 195h0M390 180h0M395 170h0M400 155h0M405 140h0M410 130h0M415 110h0M420 70h0M425 58h0M430 56h0M435 60h0M440 64h0M445 58h0M450 65h0M465 210h0M470 213h0M478 208h0M482 214h0M488 203h0M495 205h0M500 198h0M505 210h0M510 206h0M515 214h0M520 200h0M525 190h0M530 175h0M536 161h0M540 150h0M548 140h0M552 117h0M556 104h0M562 90h0M568 91h0M575 100h0M580 108h0M585 132h0M590 129h0M595 140h0M600 130h0M605 110h0M610 100h0M615 94h0M620 88h0M625 79h0M630 70h0M640 60h0M563 193h0M568 194h0M572 200h0M645 59h0M653 59h0M661 59h0M669 59h0M677 59h0M685 59h0M693 59h0M701 59h0M709 59h0M717 59h0M725 59h0M733 59h0M741 59h0M749 59h0M757 59h0M765 59h0M773 59h0M781 59h0M789 59h0M797 59h0M805 59h0M813 59h0M821 59h0M829 59h0M837 59h0M845 59h0"/>
    <path stroke="var(--blue-dot)" stroke-width="6" stroke-linecap="round" fill="none" d="M102 130h0M105 65h0M110 60h0M115 58h0M120 62h0M125 65h0M132 168h0M138 160h0M145 176h0M150 165h0M155 150h0M160 168h0M165 156h0M170 164h0M175 145h0M180 150h0M185 162h0M190 170h0M195 158h0M200 165h0M205 150h0M210 168h0M215 172h0M220 180h0M225 175h0M230 190h0M235 185h0M240 200h0M245 198h0M250 188h0M255 195h0M260 190h0M265 183h0M270 200h0M275 210h0M280 190h0M285 200h0M290 203h0M295 195h0M300 188h0M305 200h0M310 215h0M315 205h0M320 198h0M325 210h0M330 215h0M335 205h0M340 195h0M345 200h0M350 180h0M357 124h0M362 112h0M366 92h0M370 88h0M375 86h0M380 80h0M385 90h0M392 100h0M396 135h0M400 145h0M405 158h0M410 190h0M415 185h0M420 178h0M425 160h0M430 140h0M435 130h0M440 115h0M445 108h0M450 100h0M455 92h0M460 80h0M465 70h0M470 62h0M475 57h0M480 60h0M485 57h0M492 57h0M499 57h0M506 57h0M513 57h0M520 57h0M527 57h0M534 57h0M541 57h0M548 57h0M555 57h0M562 57h0M569 57h0M576 57h0M583 57h0M590 57h0M597 57h0M604 57h0M611 57h0M618 57h0M625 57h0M632 57h0M639 57h0M646 57h0M653 57h0M660 57h0M667 57h0M674 57h0M681 57h0M688 57h0M695 57h0M702 57h0M709 57h0M716 57h0M723 57h0M730 57h0M737 57h0M744 57h0M751 57h0M758 57h0M765 57h0M772 57h0M779 57h0M786 57h0M793 57h0M800 57h0M807 57h0M814 57h0M821 57h0M828 57h0M835 57h0M842 57h0M849 57h0M856 57h0M862 57h0"/>
    <path stroke="#3a9a3a" stroke-width="6" stroke-linecap="round" d="M855 224h0M860 224h0M866 224h0"/>

    <text x="955" y="62" font-family="serif" font-size="11" fill="#444">Names</text>
    <g>
      <circle cx="938" cy="58" r="3" fill="#8fb4d9"/><circle cx="938" cy="74" r="3" fill="#f4b183"/>
      <circle cx="938" cy="91" r="3" fill="#3a9a3a"/><circle cx="938" cy="108" r="3" fill="#e07a7a"/>
      <circle cx="938" cy="124" r="3" fill="#c5a3de"/><circle cx="938" cy="141" r="3" fill="#b09a90"/>
      <circle cx="938" cy="158" r="3" fill="#efb1d4"/><circle cx="938" cy="174" r="3" fill="#bbb"/>
      <circle cx="938" cy="191" r="3" fill="var(--olive-dot)"/><circle cx="938" cy="207" r="3" fill="#8fd6de"/>
      <circle cx="938" cy="224" r="3" fill="var(--blue-dot)"/>
    </g>
  </svg>
</section>
</body>
</html>
```